Hartwell Estates Business Cards

I would like a business card that includes myself and my partner.
Includes: Logo, office #, email, website, our names, our numbers and possibly the address. I would also like the logo to be embossed and the card to be horizontal.
There is a photo of our yard signs to give you an idea of the colors of our business.

Target Market(s)

Everyone in real estate market.
We are in a rural area. Our clientele are from all socioeconomic backgrounds.

Industry/Entity Type

Real Estate Agent

Contact Information for Business Card

Company Name: Hartwell Estates
Our Names, Titles & Cell #'s : Dana Pembrook-Broker (555).317.6624, Marla Pembrook-Realtor (555).609.1385
Office #: (555).240.3918
Website: hartwellestates-demo.com
Joint Email: pembrook@hartwellestates-demo.com
Office Address: 418B W. Calloway Ave.
Fernvale, LA. 70913

Font styles to use
Serif

Requirements
Must have
• HORIZONTAL, Logo, Myself and my partners names, Our cell #'s, our office #, our website, our email address
Nice to have
• Embossed logo, office address, our titles.

```html
<!DOCTYPE html>
<html lang="en">
<head>
<meta charset="utf-8">
<title>Hartwell Estates Business Cards</title>
<link rel="stylesheet" href="https://fonts.googleapis.com/css2?family=Libre+Baskerville:wght@700&family=PT+Sans:wght@400;700&display=swap">
<style>
  :root {
    --purple-deep: #3f1560;
    --purple: #55237a;
    --purple-light: #6a3690;
    --white: #ffffff;
    --paper: #f3f1f5;
    --backdrop: #e9e6ec;
    --text-light: #f1eaf6;
    --card-w: 560px;
    --card-h: 320px;
  }
  * { box-sizing: border-box; margin: 0; padding: 0; }
  html, body {
    width: 1200px;
    height: 843px;
    overflow: hidden;
    background: var(--backdrop);
  }
  .stage {
    width: 1200px;
    height: 843px;
    display: flex;
    align-items: center;
    justify-content: center;
    gap: 40px;
  }
  .card {
    position: relative;
    width: var(--card-w);
    height: var(--card-h);
    border-radius: 4px;
    overflow: hidden;
    box-shadow: 0 6px 18px rgba(40, 10, 60, 0.18);
  }

  /* Back of card */
  .card-back {
    background: linear-gradient(100deg, var(--purple-deep) 0%, var(--purple) 45%, var(--purple-light) 55%, var(--purple) 70%, var(--purple-deep) 100%);
    display: flex;
    flex-direction: column;
    align-items: center;
    justify-content: center;
    color: var(--white);
  }
  .back-name {
    font-family: "Libre Baskerville", serif;
    font-weight: 700;
    font-size: 34px;
    letter-spacing: 1px;
    text-transform: uppercase;
    color: var(--white);
  }
  .back-web {
    font-family: "PT Sans", sans-serif;
    font-size: 15px;
    margin-top: 6px;
    color: var(--text-light);
  }

  /* Front of card */
  .card-front {
    background: var(--white);
  }
  .front-brand {
    position: absolute;
    top: 0;
    left: 0;
    right: 0;
    height: 148px;
    display: flex;
    align-items: center;
    justify-content: center;
    gap: 14px;
    padding-left: 120px;
  }
  .brand-dot {
    width: 34px;
    height: 34px;
    border-radius: 50%;
    background: var(--purple);
  }
  .brand-name {
    font-family: "Libre Baskerville", serif;
    font-weight: 700;
    font-size: 26px;
    color: var(--purple);
    text-transform: uppercase;
    letter-spacing: 0.5px;
  }
  .front-band {
    position: absolute;
    top: 148px;
    left: 0;
    right: 0;
    height: 156px;
    background: linear-gradient(100deg, var(--purple-deep) 0%, var(--purple) 30%, var(--purple-light) 38%, var(--purple) 48%, var(--purple-deep) 100%);
    color: var(--white);
    font-family: "PT Sans", sans-serif;
    display: flex;
    justify-content: space-between;
    padding: 18px 28px 14px 28px;
  }
  .agents { display: flex; flex-direction: column; gap: 12px; }
  .agent-name {
    font-size: 21px;
    font-weight: 400;
  }
  .agent-title {
    font-size: 14px;
    margin-left: 6px;
  }
  .agent-phone {
    font-size: 14px;
    margin-top: 1px;
    color: var(--text-light);
  }
  .office {
    align-self: flex-end;
    text-align: right;
    font-size: 15px;
    font-style: normal;
    line-height: 1.35;
    color: var(--text-light);
  }
  .office strong { font-weight: 700; color: var(--white); }
  .front-strip {
    position: absolute;
    left: 0;
    right: 0;
    bottom: 0;
    height: 16px;
    background: var(--paper);
  }
</style>
</head>
<body>
  <main class="stage">
    <section class="card card-back" aria-label="Card back">
      <div class="back-name">Hartwell Estates</div>
      <div class="back-web">www.hartwellestates-demo.com</div>
    </section>

    <section class="card card-front" aria-label="Card front">
      <div class="front-brand">
        <span class="brand-dot" aria-hidden="true"></span>
        <span class="brand-name">Hartwell Estates</span>
      </div>
      <div class="front-band">
        <div class="agents">
          <div class="agent">
            <div><span class="agent-name">Dana Pembrook,</span><span class="agent-title">Broker</span></div>
            <div class="agent-phone">(555).317.6624</div>
          </div>
          <div class="agent">
            <div><span class="agent-name">Marla Pembrook,</span><span class="agent-title">Realtor</span></div>
            <div class="agent-phone">(555).609.1385</div>
          </div>
        </div>
        <address class="office">
          418B W. Calloway Ave.<br>
          Fernvale, LA. 70913<br>
          <strong>Phone:</strong> (555).240.3918<br>
          pembrook@hartwellestates-demo.com<br>
          hartwellestates-demo.com
        </address>
      </div>
      <div class="front-strip"></div>
    </section>
  </main>
</body>
</html>
```